Business card design Needed for new logo / Construction business, home extensions and new builds

We need a business card design using our new logo files which i will attach to this project :)

We are a small construction business specialising in home extensions, new builds and property development. We are very ambitious and would appreciate professional and elegant designs for our new business card.

Very serious about using the services on MakerQuarry and recently acquired our new logo from here :)

Please get involved, i will feedback when i can as i am very busy but can respond daily, thanks

Target Market(s)

People that want to build onto their houses, new building developments or adding too their existing property

Industry/Entity Type

Construction

Contact Information for Business Card

Renwick Tolliver Construction, Lionel Ashby (Managing Director), Tel 07822254961, email - info@renwick-tolliver, www.renwick-tolliver.co.uk

Colors

Designer to choose colors to be used in the design.

Requirements
Must have
• I like a deep grey on the back please. A lot of you have provided black from and back, try mixing things up a little. The black looks cool 😎 Thanks

```html
<!DOCTYPE html>
<html lang="en">
<head>
<meta charset="utf-8">
<title>Renwick Tolliver Construction – Business Card</title>
<link rel="stylesheet" href="https://fonts.googleapis.com/css2?family=Cinzel:wght@500&family=Arimo:wght@400;700&display=swap">
<style>
  :root {
    --backdrop: #1f1f21;
    --gold-light: #efcd85;
    --gold-mid: #d6a453;
    --gold-deep: #a86f22;
    --charcoal: #2e2e30;
    --silver: #c9cbd0;
    --silver-dark: #7d8087;
    --ink: #1b1b1b;
    --brand-gold: #d9a84a;
  }
  * { margin: 0; padding: 0; box-sizing: border-box; }
  html, body {
    width: 1200px; height: 960px; overflow: hidden;
    background: var(--backdrop);
  }
  .canvas {
    position: relative; width: 1200px; height: 960px;
  }
  .card {
    position: absolute; left: 250px; width: 700px; height: 410px;
    border-radius: 26px; overflow: hidden;
    background: radial-gradient(ellipse at 50% 45%, var(--gold-light) 0%, var(--gold-mid) 50%, var(--gold-deep) 100%);
    box-shadow: 0 14px 30px rgba(0,0,0,0.45);
  }
  .card-front { top: 40px; }
  .card-back { top: 510px; }

  .brand-name {
    font-family: 'Cinzel', serif; font-weight: 500;
    letter-spacing: 2px; text-align: center; line-height: 1.3;
  }
  .card-front .brand-name {
    position: absolute; left: 0; right: 0; top: 160px;
    font-size: 30px; color: var(--ink);
  }
  .wave { position: absolute; inset: 0; width: 700px; height: 410px; }
  .card-back .brand-name {
    position: absolute; left: 60px; top: 70px; width: 300px;
    font-size: 22px; color: var(--brand-gold);
  }
  .contact {
    position: absolute; right: 44px; top: 255px;
    font-family: 'Arimo', sans-serif; color: var(--ink); text-align: right;
  }
  .contact-name { font-size: 28px; font-weight: 700; }
  .contact-role { font-size: 17px; margin-bottom: 14px; }
  .contact-line {
    display: flex; justify-content: flex-end; align-items: center; gap: 8px;
    font-size: 18px; line-height: 1.35;
  }
  .contact-line svg { width: 14px; height: 14px; flex: none; }
</style>
</head>
<body>
<main class="canvas">
  <section class="card card-front">
    <div class="brand-name">Renwick Tolliver<br>Construction</div>
  </section>

  <section class="card card-back">
    <svg class="wave" viewBox="0 0 700 410" aria-hidden="true">
      <defs>
        <linearGradient id="silverBand" x1="0" y1="0" x2="1" y2="0">
          <stop offset="0" stop-color="var(--silver-dark)"/>
          <stop offset="0.4" stop-color="var(--silver)"/>
          <stop offset="1" stop-color="var(--silver-dark)"/>
        </linearGradient>
      </defs>
      <path d="M0,0 H700 V212 C600,212 520,240 420,287 C330,327 200,342 120,302 C60,272 20,227 0,202 Z" fill="url(#silverBand)"/>
      <path d="M0,0 H700 V198 C600,198 520,226 420,272 C330,312 200,326 120,287 C60,257 20,212 0,188 Z" fill="var(--charcoal)"/>
    </svg>
    <div class="brand-name">Renwick Tolliver<br>Construction</div>
    <div class="contact">
      <div class="contact-name">Lionel Ashby</div>
      <div class="contact-role">Managing Director</div>
      <div class="contact-line">07822254961
        <svg viewBox="0 0 16 16"><path d="M3 1l3 0 1 4-2 1c1 2 3 4 5 5l1-2 4 1v3c0 1-1 2-2 2C7 15 1 9 1 3c0-1 1-2 2-2z" fill="var(--ink)"/></svg>
      </div>
      <div class="contact-line">info@renwick-tolliver
        <svg viewBox="0 0 16 16"><rect x="1" y="3" width="14" height="10" fill="var(--ink)"/><path d="M1 3l7 6 7-6" fill="none" stroke="var(--gold-mid)" stroke-width="1.2"/></svg>
      </div>
      <div class="contact-line">www.renwick-tolliver.co.uk
        <svg viewBox="0 0 16 16"><circle cx="8" cy="8" r="7" fill="var(--ink)"/><path d="M1 8h14M8 1c-3 4-3 10 0 14M8 1c3 4 3 10 0 14" fill="none" stroke="var(--gold-mid)" stroke-width="1"/></svg>
      </div>
    </div>
  </section>
</main>
</body>
</html>
```